Brightfen Business Card Redesign & Logo Update

We need to update our business cards to something more modern and fresh. Brightfen can provide the current color schemes and old design examples, but welcome creativity in helping us with this redesign. PLEASE NOTE that we no longer utilize the "tree" and/or "leaf" imagery in our branding. If able would apprecaite an update on the quality of our "words only" logo in Ai. / PNG formats too.

Target Market(s)

Investors, landowners, corporate partners, contractors

Industry/Entity Type

Environmental Restoration & Conservation

Contact Information for Business Card

Logo, persons name, title, mailing address, phone and email, website url

Font styles to use
Other font styles liked:
• Merriweather

Requirements
Nice to have
• Logo, persons name, title, mailing address, phone and email, website url, but open to ideams
Should not have
• No all back backgrounds

```html
<!DOCTYPE html>
<html lang="en">
<head>
<meta charset="utf-8">
<title>Brightfen Business Card</title>
<link rel="stylesheet" href="https://fonts.googleapis.com/css2?family=Bebas+Neue&family=Roboto:wght@400;500&display=swap">
<style>
  :root {
    --backdrop: #e4e4e4;
    --card: #ffffff;
    --orange: #ee7a10;
    --green: #167c35;
    --ink: #1c1c1c;
    --shadow: rgba(0, 0, 0, 0.35);
  }
  * { margin: 0; padding: 0; box-sizing: border-box; }
  html, body {
    width: 1200px;
    height: 900px;
    overflow: hidden;
    background: var(--backdrop);
  }
  .stage { position: relative; width: 1200px; height: 900px; }
  .card {
    position: absolute;
    top: 216px;
    width: 309px;
    height: 501px;
    background: var(--card);
    box-shadow: 2px 3px 4px var(--shadow);
    overflow: hidden;
  }
  .card--front { left: 279px; border-radius: 0 66px 0 66px; }
  .card--back { left: 617px; border-radius: 66px 0 66px 0; }
  .card__texture {
    position: absolute;
    inset: 0;
    background: linear-gradient(90deg, #fdfbf8 0%, #f8fbf8 50%, #fdfbf8 100%);
  }
  .company-name {
    position: absolute;
    left: 0;
    right: 0;
    text-align: center;
    font-family: "Roboto", sans-serif;
    font-weight: 500;
    color: var(--green);
    line-height: 1;
  }
  .card--front .company-name { top: 226px; font-size: 44px; }
  .card--back .company-name { top: 140px; font-size: 50px; }

  .holder {
    position: absolute;
    left: 32px;
    top: 304px;
    font-family: "Roboto", sans-serif;
    color: var(--ink);
  }
  .holder__name {
    font-family: "Bebas Neue", sans-serif;
    font-size: 28px;
    line-height: 1;
  }
  .holder__first { color: var(--orange); }
  .holder__last { color: var(--green); }
  .holder__title { font-size: 14.5px; font-weight: 500; margin-top: 1px; }
  .contact { list-style: none; margin-top: 13px; }
  .contact__item {
    display: flex;
    align-items: center;
    gap: 5px;
    font-size: 15px;
    line-height: 18px;
  }
  .contact__icon { width: 13px; height: 13px; flex: none; }
  .address { margin-top: 14px; font-size: 15px; line-height: 18px; }
</style>
</head>
<body>
<main class="stage">
  <section class="card card--front" aria-label="Card front">
    <div class="card__texture" role="img" aria-label="Faint repeating company name pattern in pale orange and green"></div>
    <p class="company-name">Brightfen</p>
  </section>

  <section class="card card--back" aria-label="Card back">
    <p class="company-name">Brightfen</p>
    <div class="holder">
      <p class="holder__name"><span class="holder__first">Daniel</span> <span class="holder__last">Harper</span></p>
      <p class="holder__title">Managing Director</p>
      <ul class="contact">
        <li class="contact__item">
          <svg class="contact__icon" viewBox="0 0 24 24" aria-hidden="true"><path fill="var(--orange)" d="M6.6 10.8a15.2 15.2 0 0 0 6.6 6.6l2.2-2.2c.3-.3.7-.4 1-.2 1.1.4 2.3.6 3.6.6.6 0 1 .4 1 1V20c0 .6-.4 1-1 1C10.6 21 3 13.4 3 4c0-.6.4-1 1-1h3.5c.6 0 1 .4 1 1 0 1.3.2 2.5.6 3.6.1.3 0 .7-.2 1z"/></svg>
          044-987 654 321
        </li>
        <li class="contact__item">
          <svg class="contact__icon" viewBox="0 0 24 24" aria-hidden="true"><rect x="2" y="5" width="20" height="14" fill="var(--orange)"/><path d="M2 5l10 8 10-8M2 19l7-7M22 19l-7-7" stroke="#fff" stroke-width="1.6" fill="none"/></svg>
          hello@brightfen.co
        </li>
        <li class="contact__item">
          <svg class="contact__icon" viewBox="0 0 24 24" aria-hidden="true"><g fill="none" stroke="var(--orange)" stroke-width="2"><circle cx="12" cy="12" r="10"/><ellipse cx="12" cy="12" rx="4.5" ry="10"/><path d="M2 12h20M4 7h16M4 17h16"/></g></svg>
          www.brightfen.co
        </li>
      </ul>
      <p class="address">18, Marsh Lane Office Park<br>30914, Greenvale</p>
    </div>
  </section>
</main>
</body>
</html>
```